Cat-products company needs smart, yet endearing, business card

We need a business card design for a new, but up-and-running, business based in Honolulu, Hawaii. The business is Purrnest Nook Co. Our first product is the most environmentally-friendly cat grass kit ever seen on the planet. Future products, currently in the R&D phase, will include a variety of exciting cat scratchers. We also do consulting work to help apartment-dwellers make their home more cat-friendly and, in the future, plan on doing full, custom installs of structure to create high walkways for cats.

Target Market(s)

Middle-aged, apartment-dwelling, middle-class workers who own 1 or more cats and who dote on them.

Industry/Entity Type

Pet Care

Contact Information for Business Card

A striking, professional, yet warm and friendly design is what we're after.

Font styles to use
Serif
Sans Serif
Other font styles liked:
• Comfortaa

Colors

Designer to choose colors to be used in the design.

Requirements
Must have
• The company logo: (see attachment)
• The company name: Purrnest Nook Co
• The web address: www.purrnestnookco.com
• Email: support@purrnestnookco.com
• Phone: +1 (808) 571 6023
• Update (Fri Jun 30 3017 7:45pm Hawaii Time) I would like, is possible, uploaded picture of the cat grass kit on the back of the card with some text along the lines of: Purrnest Nook Co - Maker Of The Leafiest Feline Sprout Set Yet
Nice to have
• A cat picture, cartoon, real or silhouette that illustrates cats in action and/or relaxing; ie using the apartment space to live, play and relax in and being well-contented.
• Most of the website is done in the font: Comfortaa. It might be nice to continue using this for brand consistency.
Should not have
• Hard-to-read fonts.

```html
<!DOCTYPE html>
<html lang="en">
<head>
<meta charset="utf-8">
<title>Purrnest Nook Co – Business Card</title>
<link href="https://fonts.googleapis.com/css2?family=Comfortaa:wght@400;600;700&family=Quicksand:wght@400;500;700&display=swap" rel="stylesheet">
<style>
  :root {
    --stage: #857110;
    --card: #ffffff;
    --brown: #4e342e;
    --gold: #f5b31a;
    --olive-gold: #9a7d2e;
    --rule: #a88a3a;
    --icon-red: #7a1a1a;
    --text-dark: #4a2a24;
    --art-dark: #2a1a14;
    --art-warm: #e8c35a;
    --art-cool: #8fc6cf;
    --art-red: #c8333a;
  }
  * { margin: 0; padding: 0; box-sizing: border-box; }
  html, body { width: 1200px; height: 1200px; overflow: hidden; }
  body { background: var(--stage); position: relative; font-family: "Quicksand", sans-serif; }

  .card { position: absolute; width: 840px; height: 480px; background: var(--card); overflow: hidden; }
  .card--front { left: 54px; top: 126px; }
  .card--back { left: 273px; top: 663px; }

  .art { position: absolute; left: 0; top: 0; width: 840px; height: 480px; }

  .brand { position: absolute; display: flex; flex-direction: column; align-items: center; transform: translateX(-50%); }
  .brand__mark { width: 64px; height: 64px; background: var(--brown); margin-bottom: 22px; }
  .brand__name { font-family: "Comfortaa", sans-serif; font-weight: 700; color: var(--gold); font-size: 30px; white-space: nowrap; }
  .card--front .brand { left: 253px; top: 150px; }
  .card--back .brand { left: 419px; top: 160px; }

  .divider { position: absolute; left: 418px; top: 94px; width: 2px; height: 263px; background: var(--rule); }

  .person { position: absolute; left: 478px; top: 88px; font-family: "Comfortaa", sans-serif; }
  .person__name { font-size: 21px; font-weight: 600; color: var(--brown); }
  .person__name .first { color: var(--olive-gold); }
  .person__role { font-size: 13px; color: var(--brown); margin-top: 8px; }

  .contact { position: absolute; left: 478px; list-style: none; font-size: 14px; color: var(--text-dark); font-weight: 500; }
  .contact li { position: absolute; display: flex; align-items: center; white-space: nowrap; height: 20px; }
  .contact li:nth-child(1) { top: 193px; }
  .contact li:nth-child(2) { top: 252px; }
  .contact li:nth-child(3) { top: 305px; }
  .contact svg { width: 17px; height: 17px; margin-right: 42px; flex: none; }
  .contact li:nth-child(1) svg { margin-right: 40px; }

  .footer-name { position: absolute; left: 478px; top: 432px; font-size: 14px; color: var(--olive-gold); font-family: "Comfortaa", sans-serif; }

  .back-web { position: absolute; left: 419px; top: 409px; transform: translateX(-50%); font-size: 14px; font-weight: 500; color: var(--text-dark); white-space: nowrap; }
</style>
</head>
<body>

<section class="card card--front">
  <svg class="art" viewBox="0 0 840 480">
    <defs>
      <linearGradient id="artTopFront" x1="0" y1="0" x2="1" y2="1">
        <stop offset="0" stop-color="var(--art-dark)"/>
        <stop offset="0.55" stop-color="#3a2418"/>
        <stop offset="1" stop-color="var(--art-warm)"/>
      </linearGradient>
      <linearGradient id="artBottomFront" x1="0" y1="1" x2="1" y2="0">
        <stop offset="0" stop-color="var(--art-dark)"/>
        <stop offset="0.5" stop-color="#3b4a44"/>
        <stop offset="1" stop-color="var(--art-cool)"/>
      </linearGradient>
    </defs>
    <polygon role="img" aria-label="Painted folk-art illustration of a black cat among colourful swirls" points="0,0 296,0 0,270" fill="url(#artTopFront)"/>
    <polygon role="img" aria-label="Painted folk-art illustration of flowers, circles and swirls" points="840,238 840,480 570,480" fill="url(#artBottomFront)"/>
  </svg>

  <div class="brand">
    <div class="brand__mark"></div>
    <div class="brand__name">Purrnest Nook Co</div>
  </div>

  <div class="divider"></div>

  <div class="person">
    <div class="person__name"><span class="first">Malia</span> Kahale</div>
    <div class="person__role">CEO</div>
  </div>

  <ul class="contact">
    <li>
      <svg viewBox="0 0 24 24"><path fill="var(--icon-red)" d="M6.6 10.8c1.4 2.8 3.8 5.1 6.6 6.6l2.2-2.2c.3-.3.7-.4 1-.2 1.1.4 2.3.6 3.6.6.6 0 1 .4 1 1V20c0 .6-.4 1-1 1C10.6 21 3 13.4 3 4c0-.6.4-1 1-1h3.5c.6 0 1 .4 1 1 0 1.3.2 2.5.6 3.6.1.3 0 .7-.2 1L6.6 10.8z"/></svg>
      +1 (808) 571 6023
    </li>
    <li>
      <svg viewBox="0 0 24 24"><rect x="2" y="5" width="20" height="14" fill="var(--icon-red)"/><path d="M2 5l10 8 10-8M2 19l7-7M22 19l-7-7" fill="none" stroke="#fff" stroke-width="1.3"/></svg>
      support@purrnestnookco.com
    </li>
    <li>
      <svg viewBox="0 0 24 24" fill="none" stroke="var(--icon-red)" stroke-width="1.4"><circle cx="12" cy="12" r="9"/><ellipse cx="12" cy="12" rx="4" ry="9"/><path d="M3 12h18M4.5 7.5h15M4.5 16.5h15"/></svg>
      www.purrnestnookco.com
    </li>
  </ul>

  <div class="footer-name">Purrnest Nook Co</div>
</section>

<section class="card card--back">
  <svg class="art" viewBox="0 0 840 480">
    <defs>
      <linearGradient id="artTopBack" x1="0" y1="0" x2="1" y2="1">
        <stop offset="0" stop-color="var(--art-dark)"/>
        <stop offset="0.55" stop-color="#3a2418"/>
        <stop offset="1" stop-color="var(--art-warm)"/>
      </linearGradient>
      <linearGradient id="artBottomBack" x1="0" y1="1" x2="1" y2="0">
        <stop offset="0" stop-color="var(--art-dark)"/>
        <stop offset="0.5" stop-color="#3b4a44"/>
        <stop offset="1" stop-color="var(--art-cool)"/>
      </linearGradient>
    </defs>
    <polygon role="img" aria-label="Painted folk-art illustration of a black cat among colourful swirls" points="0,0 296,0 0,270" fill="url(#artTopBack)"/>
    <polygon role="img" aria-label="Painted folk-art illustration of flowers, circles and swirls" points="840,238 840,480 570,480" fill="url(#artBottomBack)"/>
  </svg>

  <div class="brand">
    <div class="brand__mark"></div>
    <div class="brand__name">Purrnest Nook Co</div>
  </div>

  <div class="back-web">www.purrnestnookco.com</div>
</section>

</body>
</html>
```